POSTER FOR NEW MUSIC-THEATRE PRODUCTION - Het Molenveldgezelschap

For our new theatre production 'Kraaienval' we're looking for a new poster design.

All details can be found in the itinerary in attachment.
Updates

Dear designers

Thanks for some really good designs up to now.
Detailed feedback will follow from next week onwards since Im abroad for business and since I have very little internet access.

kind regards
Joost Kerk

Target Market(s)

Theatres throughout Flanders (Belgium) when on tour in 2010-2011-2012. (expecting 70 performances)
Age is 14 up till 88 years old.

Requirements
Must have
• see itinerary in attachment
Nice to have
• Take a look to the poster design of our former production. We kind of liked the 'cool' look.
• Mind : use the new logo in attachment
Should not have
• too many colours.

```html
<!DOCTYPE html>
<html lang="nl">
<head>
<meta charset="utf-8">
<title>Kraaienval – Het Molenveldgezelschap</title>
<link href="https://fonts.googleapis.com/css2?family=Anton&family=Roboto+Condensed:wght@400;500;700&display=swap" rel="stylesheet">
<style>
  :root {
    --paper: #ffffff;
    --ink: #000000;
    --slate: #575364;
    --frame: #9a9a9a;
    --sheet-light: #e4d8c0;
    --sheet-mid: #cbb995;
    --sheet-dark: #a8967a;
  }
  html, body { margin: 0; padding: 0; overflow: hidden; background: var(--paper); }
  .poster {
    position: relative;
    width: 900px; height: 1200px;
    background: var(--paper);
    overflow: hidden;
    font-family: "Roboto Condensed", "Arial Narrow", sans-serif;
  }
  .poster-frame {
    position: absolute; left: 8px; top: -2px; width: 881px; height: 1190px;
    border: 1px solid var(--frame);
  }
  .presenter {
    position: absolute; left: 212px; top: 86px; margin: 0;
    font-weight: 700; font-size: 26px; letter-spacing: -0.3px;
    color: var(--ink); text-transform: uppercase; line-height: 1;
    transform: scaleY(1.3); transform-origin: left top;
  }
  .presenter .verb { color: var(--slate); }
  .title {
    position: absolute; left: 148px; top: 118px; margin: 0;
    font-family: "Anton", "Impact", sans-serif; font-weight: 400;
    font-size: 118px; line-height: 1; letter-spacing: 2px;
    text-transform: uppercase; color: var(--ink);
    transform: scaleY(1.08); transform-origin: left top;
  }
  .title .lead { color: var(--slate); }
  .artwork {
    position: absolute; left: 190px; top: 262px; width: 530px; height: 590px;
  }
  .credits {
    position: absolute; left: 0; top: 776px; width: 900px;
    text-align: center; margin: 0;
  }
  .credit { margin: 0 0 5px; }
  .credit dt {
    font-weight: 700; font-size: 16px; color: var(--ink);
    text-transform: uppercase; line-height: 18px;
  }
  .credit dd {
    margin: 0; font-size: 17px; font-weight: 500; color: var(--slate); line-height: 19px;
  }
  .partners {
    position: absolute; left: 0; top: 1092px; width: 900px; height: 80px;
  }
  .partner {
    position: absolute; display: flex; align-items: center;
    font-weight: 700; color: var(--ink);
  }
  .partner-vonk { left: 262px; top: 18px; gap: 4px; font-size: 14px; line-height: 15px; }
  .partner-host { left: 392px; top: 4px; width: 68px; flex-direction: column; gap: 6px; font-size: 15px; }
  .partner-support { left: 515px; top: 16px; flex-direction: column; align-items: flex-start; gap: 6px; }
  .mark-square { width: 10px; height: 10px; background: var(--ink); }
  .mark-circle { width: 40px; height: 40px; border-radius: 50%; background: var(--ink); }
  .badge { width: 110px; height: 18px; background: var(--slate); }
  .support-note {
    font-size: 7.5px; font-weight: 700; text-transform: uppercase; line-height: 9px; color: var(--ink);
  }
  .imprint {
    position: absolute; left: 0; top: 1178px; width: 900px; margin: 0; text-align: center;
    font-size: 6.5px; font-weight: 700; text-transform: uppercase; color: var(--ink); letter-spacing: 0.3px;
  }
</style>
</head>
<body>
<main class="poster">
  <div class="poster-frame"></div>

  <p class="presenter">Het Molenveldgezelschap <span class="verb">speelt</span></p>
  <h1 class="title"><span class="lead">Kraaien</span>val</h1>

  <svg class="artwork" viewBox="0 0 530 590" role="img" aria-label="Heraldic bird with spread wings, built from collaged sheet music in parchment tones">
    <defs>
      <radialGradient id="sheet" cx="50%" cy="50%" r="50%">
        <stop offset="0%" stop-color="var(--sheet-light)"/>
        <stop offset="55%" stop-color="var(--sheet-mid)"/>
        <stop offset="85%" stop-color="var(--sheet-dark)" stop-opacity="0.45"/>
        <stop offset="100%" stop-color="var(--sheet-dark)" stop-opacity="0"/>
      </radialGradient>
    </defs>
    <ellipse cx="265" cy="270" rx="262" ry="265" fill="url(#sheet)"/>
  </svg>

  <dl class="credits">
    <div class="credit"><dt>Tekst</dt><dd>Lies Verhaegen</dd></div>
    <div class="credit"><dt>Regie</dt><dd>Johan de Smet</dd></div>
    <div class="credit"><dt>Animatie</dt><dd>Greet Vandevelde &amp; Kobe Deprez</dd></div>
    <div class="credit"><dt>Kostuumontwerp</dt><dd>Josefien Meulemans</dd></div>
    <div class="credit"><dt>Lichtontwerp</dt><dd>Christophe van Overstraeten</dd></div>
    <div class="credit"><dt>Muziek &amp; spel</dt><dd>Jeroen Moerman, Wouter Moerman,<br>Frederik Moerman, Johan Peeters, Joost Kerk</dd></div>
  </dl>

  <section class="partners" aria-label="Partners">
    <div class="partner partner-vonk"><span class="mark-square"></span><span>Vonk<br>Produkties</span></div>
    <div class="partner partner-host"><span class="mark-circle"></span>HMG</div>
    <div class="partner partner-support">
      <span class="badge"></span>
      <span class="support-note">Met de steun van het Vlaamse Kunstenfonds<br>Stad Lierdonk en CC De Hoeve</span>
    </div>
  </section>

  <p class="imprint">V.U.: Molenveld Producties vzw &nbsp;|&nbsp; Joost Kerk &nbsp;|&nbsp; Lindestraat 12/4 &nbsp;|&nbsp; 2000 Lierdonk (België)</p>
</main>
</body>
</html>
```